Non fiction leadership Book Cover design needed for “Stay Bold: Build On Lasting Discipline”

I need a front cover design for a new book 6 X 9 traditional non-fiction book.

Title: "Stay BOLD - Build On Lasting Discipline"

The subtitle is not finalized- so use 2 lines of smaller dummy text

My brand guide is attached (please use the tan color sparingly)

I'd like to see BOLD look like it is in motion and "flying" across the page

Need CREATIVE designs and options

Do not want my picture on the front cover - I do want it on the back cover.

On the front cover I’d like to see creative use of font to create movement on “BOLD”

Target Market(s)

Business leaders

Industry/Entity Type

Aviation

Font styles to use
Other font styles liked:
• See style guide- can add additional font (modern script or san serif)

Colors
0054AA
0677BA
7BADD7
CADEEF
E8F1F8
EB3D1F
EC4F4E
F09395
F8D3D4
FCEDEE

Requirements
Must have
• Creative font use, using perspective to create movement/motion on BOLD
Should not have
• My picture on the front cover- my picture should be on the back cover

```html
<!DOCTYPE html>
<html lang="en">
<head>
<meta charset="utf-8">
<title>Stay Bold: Build On Lasting Discipline — Front Cover</title>
<link rel="stylesheet" href="https://fonts.googleapis.com/css2?family=Anton&family=Montserrat:wght@500;600;700&display=swap">
<style>
  :root {
    --blue: #0054AA;
    --blue-deep: #003a78;
    --blue-mid: #0677BA;
    --blue-soft: #7BADD7;
    --blue-pale: #CADEEF;
    --blue-mist: #E8F1F8;
    --red: #EB3D1F;
    --red-soft: #EC4F4E;
    --pink: #F09395;
    --paper: #FCFAF8;
    --stage: #8d979d;
  }
  * { margin: 0; padding: 0; box-sizing: border-box; }
  html, body {
    width: 1200px; height: 1200px; overflow: hidden;
    background: var(--stage);
  }
  .canvas { position: relative; width: 1200px; height: 1200px; }
  .cover {
    position: absolute; left: 240px; top: 60px;
    width: 720px; height: 1080px;
    background: var(--paper);
    overflow: hidden;
  }
  .cover-sky { position: absolute; inset: 0; width: 720px; height: 1080px; }
  .tagline {
    position: absolute; top: 40px; left: 0; right: 0;
    text-align: center;
    font-family: "Montserrat", sans-serif;
    font-weight: 500; font-size: 15px; line-height: 1.35;
    color: var(--blue-mist);
  }
  .aircraft-mark {
    position: absolute; left: 310px; top: 112px;
    width: 100px; height: 150px;
    background: radial-gradient(circle, var(--blue-pale) 0%, rgba(202,222,239,0.35) 65%, rgba(202,222,239,0) 100%);
    border-radius: 50%;
  }
  .title-art { position: absolute; left: 0; top: 300px; width: 720px; height: 580px; }
  .title-art text { font-family: "Anton", sans-serif; }
  .subtitle-band {
    position: absolute; left: 92px; top: 884px;
    width: 540px; height: 80px;
    background: var(--blue);
    display: flex; align-items: center; justify-content: center;
    font-family: "Montserrat", sans-serif;
    font-weight: 600; font-size: 25px; letter-spacing: 0.5px;
    color: var(--paper);
  }
  .author {
    position: absolute; left: 0; right: 0; top: 990px;
    text-align: center;
    font-family: "Montserrat", sans-serif;
    font-weight: 600; font-size: 38px;
    color: var(--blue);
  }
</style>
</head>
<body>
<div class="canvas">
  <main class="cover">
    <svg class="cover-sky" viewBox="0 0 720 1080" aria-hidden="true">
      <defs>
        <linearGradient id="skyShade" x1="0" y1="0" x2="1" y2="0.6">
          <stop offset="0" stop-color="var(--blue-mid)"/>
          <stop offset="0.6" stop-color="var(--blue-deep)"/>
        </linearGradient>
      </defs>
      <polygon points="0,0 720,0 720,355 360,270 0,355" fill="url(#skyShade)"/>
    </svg>

    <p class="tagline">Lorem ipsum dolor sit amet, consectetuer adipiscing<br>sed diam nonummy nibh euismod tincidunt</p>

    <div class="aircraft-mark" role="img" aria-label="White silhouette of a helicopter seen from above, resting on the peak"></div>

    <svg class="title-art" viewBox="0 0 720 580" role="img" aria-label="Stay BOLD">
      <defs>
        <linearGradient id="boldFill" x1="0" y1="0" x2="1" y2="1">
          <stop offset="0" stop-color="var(--pink)"/>
          <stop offset="0.45" stop-color="var(--red-soft)"/>
          <stop offset="1" stop-color="var(--red)"/>
        </linearGradient>
        <linearGradient id="trailFade" x1="0" y1="0" x2="1" y2="0">
          <stop offset="0" stop-color="var(--red-soft)" stop-opacity="0"/>
          <stop offset="1" stop-color="var(--red-soft)" stop-opacity="0.85"/>
        </linearGradient>
        <linearGradient id="trailFadeBlue" x1="0" y1="0" x2="1" y2="0">
          <stop offset="0" stop-color="var(--blue-soft)" stop-opacity="0"/>
          <stop offset="1" stop-color="var(--blue-soft)" stop-opacity="0.9"/>
        </linearGradient>
        <g id="boldWord">
          <text x="40" y="560" font-size="250" textLength="125" lengthAdjust="spacingAndGlyphs">B</text>
          <text x="180" y="560" font-size="300" textLength="145" lengthAdjust="spacingAndGlyphs">O</text>
          <text x="340" y="560" font-size="350" textLength="120" lengthAdjust="spacingAndGlyphs">L</text>
          <text x="475" y="560" font-size="400" textLength="165" lengthAdjust="spacingAndGlyphs">D</text>
        </g>
      </defs>

      <text x="360" y="190" text-anchor="middle" font-size="122" fill="var(--blue)"
            textLength="200" lengthAdjust="spacingAndGlyphs">STAY</text>

      <g class="motion-trails">
        <rect x="0" y="390" width="120" height="8" fill="url(#trailFade)"/>
        <rect x="0" y="430" width="95" height="5" fill="url(#trailFadeBlue)"/>
        <rect x="0" y="470" width="130" height="10" fill="url(#trailFade)"/>
        <rect x="0" y="512" width="85" height="5" fill="url(#trailFadeBlue)"/>
        <rect x="0" y="545" width="105" height="7" fill="url(#trailFade)"/>
      </g>

      <g transform="translate(99,0) skewX(-10)">
        <use href="#boldWord" transform="translate(-7,-5)" fill="var(--blue-deep)"/>
        <use href="#boldWord" fill="url(#boldFill)"/>
      </g>
    </svg>

    <div class="subtitle-band">BUILD ON LASTING DISCIPLINE</div>
    <p class="author">Margaret Ellison</p>
  </main>
</div>
</body>
</html>
```